Business card por a urban DJ, up scale audience target

Need a sober design, modern, conservative colors but i can consider some options, y play rnb, hip hop, EDM and top40.

Business card for contact and personal info, double sided, use logo attrached please; im 42 so i need a card acording to my age an target audience.

Target Market(s)

Adult people, up scale audience

Industry/Entity Type

Music Download

Contact Information for Business Card

Cel (318) 4207265518 www.lumadrift.com

Requirements
Must have
• open mind
Nice to have
• open mind
Should not have
• DJ

```html
<!DOCTYPE html>
<html lang="en">
<head>
<meta charset="utf-8">
<title>Lumadrift Business Card</title>
<link rel="stylesheet" href="https://fonts.googleapis.com/css2?family=Jost:wght@400;500;700&display=swap">
<style>
  :root {
    --stage: #e4e2de;
    --ink: #151515;
    --band-dark: #111111;
    --band-light: #3a3a3a;
    --paper: #ffffff;
    --paper-text: #1c1c1c;
    --band-text: #ffffff;
  }
  * { margin: 0; padding: 0; box-sizing: border-box; }
  html, body {
    width: 1200px;
    height: 950px;
    overflow: hidden;
    background: var(--stage);
    font-family: "Jost", "Futura", sans-serif;
  }
  .stage {
    width: 1200px;
    height: 950px;
    display: flex;
    align-items: center;
    justify-content: center;
  }
  .card {
    position: relative;
    width: 1000px;
    height: 571px;
    background: var(--paper);
    overflow: hidden;
    box-shadow: 0 12px 30px rgba(0,0,0,0.25);
  }
  .name-band {
    position: absolute;
    left: 0; top: 0;
    width: 100%;
    height: 160px;
    background: linear-gradient(100deg, var(--band-dark) 0%, var(--band-light) 45%, var(--band-dark) 100%);
    display: flex;
    align-items: flex-end;
    justify-content: space-between;
    padding: 0 50px 28px;
    color: var(--band-text);
  }
  .holder-name {
    font-size: 40px;
    font-weight: 500;
    letter-spacing: 1px;
  }
  .holder-title {
    font-size: 30px;
    font-weight: 500;
    align-self: flex-start;
    padding-top: 30px;
  }
  .brand {
    position: absolute;
    left: 0; top: 160px;
    width: 100%;
    height: 300px;
    display: flex;
    align-items: center;
    justify-content: center;
    gap: 22px;
  }
  .brand-mark {
    width: 34px;
    height: 34px;
    background: var(--ink);
  }
  .brand-name {
    font-size: 120px;
    font-weight: 700;
    color: var(--ink);
    letter-spacing: 4px;
    line-height: 1;
  }
  .contact-phone {
    position: absolute;
    left: 50px;
    bottom: 34px;
    font-size: 34px;
    font-weight: 400;
    color: var(--paper-text);
    letter-spacing: 1px;
  }
  .web-band {
    position: absolute;
    right: 0; bottom: 0;
    width: 380px;
    height: 110px;
    background: var(--band-dark);
    color: var(--band-text);
    display: flex;
    align-items: center;
    justify-content: flex-end;
    padding-right: 50px;
    font-size: 30px;
    letter-spacing: 1px;
  }
</style>
</head>
<body>
  <main class="stage">
    <article class="card">
      <header class="name-band">
        <span class="holder-name">MARCO REYES</span>
        <span class="holder-title">CEO/FOUNDER</span>
      </header>
      <div class="brand">
        <span class="brand-mark"></span>
        <span class="brand-name">LUMA</span>
      </div>
      <p class="contact-phone">(318) 4207265518</p>
      <p class="web-band">www.lumadrift.com</p>
    </article>
  </main>
</body>
</html>
```